TL - business card

Tallow Partners is an insurance brokerage firm, inovative, proactive, vigorous, which aims to become the leader of the insurance brokers in Anfrica. We should like to get some designs which should be avoided also in Gray / Metallic for the Administration and Orange / Blue for the Managers (ike in the picture sent). The Blue / Green logo is not the correct one, but the source of the file. Please adjust the color accordingly for the business cards. 1 / Orange / Blue 2 / Gray / Metallic We want something classic but which is transmitted strenght, inovation, modernity and most of all, rapidity. We want something start-up like, very punchy and catching eye remaining profesional at the same time. Name: Dorian Whitlock Function: Managing Director Address: N ° 17/18 Rua Veloso - R / C 2B Direita - Bairro Mutamba - Luanda Tel: (+244) 947 582 316 Email: dorian.whitlock@tallow-p.example Website: www.tallow-p. example We want classic in the front and creative, colorfull at the back. The cards will be printed in relief, with very high quality of paper.
Insurance Broker
Colors
Designer to choose colors to be used in the design.

```html
<!DOCTYPE html>
<html lang="en">
<head>
<meta charset="utf-8">
<title>TL - business card</title>
<link rel="stylesheet" href="https://fonts.googleapis.com/css2?family=Montserrat:wght@400;500;700&display=swap">
<style>
  :root {
    --bg: #d4d4d4;
    --brand-blue: #1f9bd3;
    --brand-orange: #f39a1a;
    --paper: #f6f6f5;
    --ink: #2a2a2a;
    --ink-soft: #555555;
    --white: #ffffff;
  }
  * { margin: 0; padding: 0; box-sizing: border-box; }
  html, body {
    width: 1200px; height: 784px; overflow: hidden;
    background: var(--bg);
    font-family: "Montserrat", sans-serif;
  }
  .canvas {
    width: 1200px; height: 784px;
    display: flex; align-items: center; justify-content: center; gap: 90px;
  }
  .card {
    width: 320px; height: 560px; position: relative;
    box-shadow: 0 10px 24px rgba(0,0,0,0.14);
  }

  /* Front: blue */
  .card--front { background: var(--brand-blue); }
  .front-mark {
    position: absolute; top: 110px; left: 50%; transform: translateX(-50%);
    width: 150px; height: 150px;
  }
  .front-name {
    position: absolute; left: 44px; bottom: 64px;
    color: var(--white); font-weight: 700; font-size: 19px; letter-spacing: 1px;
    text-transform: uppercase;
  }

  /* Back: white */
  .card--back { background: var(--paper); padding: 56px 0 0 40px; }
  .back-brand { display: flex; align-items: center; gap: 14px; margin-bottom: 40px; }
  .back-brand__name {
    color: var(--brand-orange); font-weight: 700; font-size: 17px; letter-spacing: 0.5px;
    text-transform: uppercase;
  }
  .back-brand__dot { width: 64px; height: 64px; flex: none; }
  .person__name {
    color: var(--brand-blue); font-weight: 700; font-size: 19px; letter-spacing: 0.5px;
    text-transform: uppercase;
  }
  .person__role {
    color: var(--ink-soft); font-size: 9px; letter-spacing: 1.2px; text-transform: uppercase;
    margin-top: 3px;
  }
  .divider {
    width: 30px; height: 1px; background: var(--brand-orange); margin: 22px 0 20px;
  }
  .contact__phone { color: var(--ink); font-weight: 500; font-size: 15px; letter-spacing: 1px; }
  .contact__line {
    color: var(--ink-soft); font-size: 9px; letter-spacing: 1px; text-transform: uppercase;
    line-height: 1.6;
  }
  .contact__phone + .contact__line { margin-top: 4px; }
</style>
</head>
<body>
<main class="canvas">
  <section class="card card--front" aria-label="Card front">
    <svg class="front-mark" viewBox="0 0 150 150" aria-hidden="true">
      <circle cx="75" cy="75" r="62" fill="none" stroke="var(--brand-orange)" stroke-width="10"/>
    </svg>
    <p class="front-name">Tallow-Partners</p>
  </section>

  <section class="card card--back" aria-label="Card back">
    <div class="back-brand">
      <span class="back-brand__name">Tallow-Partners</span>
      <svg class="back-brand__dot" viewBox="0 0 64 64" aria-hidden="true">
        <circle cx="32" cy="32" r="27" fill="none" stroke="var(--brand-blue)" stroke-width="5"/>
      </svg>
    </div>

    <h1 class="person__name">Dorian Whitlock</h1>
    <p class="person__role">Managing Director</p>

    <div class="divider"></div>

    <p class="contact__phone">(+244) 947 582 316</p>
    <p class="contact__line">dorian.whitlock@tallow-p.example</p>

    <div class="divider"></div>

    <p class="contact__line">N °17/18 Rua Veloso</p>
    <p class="contact__line">R / C 2B Direita</p>
    <p class="contact__line">Bairro Mutamba - Luanda</p>

    <div class="divider"></div>

    <p class="contact__line">www.tallow-p.example</p>
  </section>
</main>
</body>
</html>
```